Brightwave Reach - Business Card

We need a business card for a Social Media Marketing company that specializes in online marketing for small businesses in Canada using common Social Media platforms such as Pixlora, Chatterly, Blinkpost & Quibber.

I have uploaded a copy of our logo which I would like utilized in the business card. We would like the business card to be modern yet classy design.

Our website is www.brightwavereach.ca

Industry/Entity Type

Marketing

Contact Information for Business Card

Email: info@brightwavereach.ca
Website: www.brightwavereach.ca
Telephone: 604-555-0193

Colors

Designer to choose colors to be used in the design.

Requirements
Must have
• Social Media icons on reverse
• Please add some designs with color.

```html
<!DOCTYPE html>
<html lang="en">
<head>
<meta charset="utf-8">
<title>Brightwave Reach – Business Card</title>
<link rel="stylesheet" href="https://fonts.googleapis.com/css2?family=Saira+Condensed:wght@400;500;700&display=swap">
<style>
  :root {
    --backdrop: #e4e5e6;
    --card: #3b4043;
    --ink: #f2f3f3;
    --ink-soft: #d9dcdd;
    --accent: #1fa6d6;
    --leaf: #e6e8e8;
  }
  * { box-sizing: border-box; margin: 0; padding: 0; }
  html, body { width: 1200px; height: 900px; overflow: hidden; }
  body {
    background: var(--backdrop);
    font-family: "Saira Condensed", "Arial Narrow", sans-serif;
    position: relative;
  }
  .card {
    position: absolute;
    width: 560px;
    height: 320px;
    background: var(--card);
    border-radius: 4px;
    box-shadow: 0 10px 26px rgba(0,0,0,.22);
  }
  .card--front { left: 150px; top: 80px; }
  .card--back { left: 490px; top: 480px; }

  .brand {
    position: absolute;
    left: 50%; top: 50%;
    transform: translate(-50%, -50%);
    display: flex;
    align-items: center;
    gap: 12px;
  }
  .brand__mark {
    width: 16px; height: 16px;
    background: var(--ink);
  }
  .brand__name {
    color: var(--ink);
    font-weight: 700;
    font-size: 34px;
    line-height: 1;
    letter-spacing: 1px;
    text-transform: uppercase;
    white-space: nowrap;
  }

  .leaf-art {
    position: absolute;
    left: 64px; top: 56px;
    width: 38px; height: 42px;
    border-radius: 50% 50% 10% 10%;
    background: var(--leaf);
    opacity: .9;
  }
  .contact-block {
    position: absolute;
    left: 118px; top: 112px;
  }
  .phone {
    color: var(--ink);
    font-weight: 700;
    font-size: 30px;
    line-height: 1;
    letter-spacing: 3px;
    white-space: nowrap;
  }
  .accent-bar {
    display: block;
    margin: 14px 0 0 2px;
    width: 34px; height: 4px;
    background: var(--accent);
  }
  .contact {
    margin: 10px 0 0 2px;
    color: var(--ink-soft);
    font-size: 15px;
    letter-spacing: 2px;
    line-height: 22px;
    white-space: nowrap;
  }
  .social {
    margin: 10px 0 0 2px;
    display: flex;
    gap: 10px;
    color: var(--accent);
    font-size: 9px;
    line-height: 1;
    letter-spacing: 1px;
    list-style: none;
  }
</style>
</head>
<body>
  <section class="card card--front" aria-label="Card front">
    <div class="brand">
      <span class="brand__mark"></span>
      <span class="brand__name">Brightwave Reach</span>
    </div>
  </section>

  <section class="card card--back" aria-label="Card back">
    <div class="leaf-art" role="img" aria-label="White distressed maple leaf illustration"></div>
    <div class="contact-block">
      <p class="phone">[604-555-0193]</p>
      <span class="accent-bar"></span>
      <p class="contact">info@brightwavereach.ca<br>www.brightwavereach.ca</p>
      <ul class="social">
        <li>Chatterly</li>
        <li>Quibber</li>
        <li>Vidora</li>
      </ul>
    </div>
  </section>
</body>
</html>
```